Creative, fresh business card design for Ripplecraft Facades

We need a fresh, creative business card design for Ripplecraft Facades. We are the manufacturer of Ripplecraft Facades in Australia. Wall panels are 2400 x 1200mm panels made from MDF and feature 3D patterns on the face of the panel. The colours to be used are green, silver/grey and white RGB
Red 187
Green 207
Blue 65.

An idea is to possibly use a watermark of one of our designs as a background (like on the "Grids" design on the left hand side of page 2 of our brochure).

Target Market(s)

Interior designers, architects, builders and home renovators

Industry/Entity Type

Business

Contact Information for Business Card

Details to go on the card are:
Our logo (attached),
Slogan: "Decorative panels for interiors and exteriors",
Contact name,
Position,
Mobile phone number,
Business address,
Business phone,
Business fax,
Website and
Email address.

I have attached a few images of our panels and our brochure for reference.

The colours of the business card should feature our logo colours which are: RGB
Red 187
Green 207
Blue 65

Requirements
Must have
• Very modern fonts and design. Some of the designs shown especially the "Prisms" design which is a popular design.
Nice to have
• Creative but simple design. Very contemporary.
Should not have
• Anything ornate or old fashioned.

```html
<!DOCTYPE html>
<html lang="en">
<head>
<meta charset="utf-8">
<title>Ripplecraft Facades – Business Card</title>
<link rel="stylesheet" href="https://fonts.googleapis.com/css2?family=Source+Sans+3:wght@400;600;700&display=swap">
<style>
  :root {
    --stage: #3a3a3a;
    --lime: #bbcf41;
    --lime-soft: #c2d452;
    --paper: #f3f3f3;
    --paper-shade: #e6e6e6;
    --ink: #4a4a4a;
    --silver: #8f8f8f;
    --white: #ffffff;
  }
  * { margin: 0; padding: 0; box-sizing: border-box; }
  html, body {
    width: 1200px; height: 900px; overflow: hidden;
    background: var(--stage);
    font-family: "Source Sans 3", Arial, sans-serif;
  }
  .stage { position: relative; width: 1200px; height: 900px; }
  .card {
    position: absolute; top: 170px;
    width: 347px; height: 561px;
    box-shadow: 0 2px 8px rgba(0,0,0,.35);
    text-align: center; overflow: hidden;
  }
  .card-front { left: 259px; }
  .card-back { left: 631px; }
  .texture { position: absolute; inset: 0; }
  .card-front .texture {
    background: radial-gradient(ellipse at 50% 40%, var(--white) 0%, var(--paper) 55%, var(--paper-shade) 100%);
  }
  .card-back .texture {
    background: radial-gradient(ellipse at 50% 30%, var(--lime-soft) 0%, var(--lime) 70%);
  }
  .content { position: absolute; inset: 0; }
  .brand { position: absolute; left: 0; right: 0; display: flex; flex-direction: column; align-items: center; }
  .brand-mark { width: 62px; height: 62px; }
  .brand-name { font-weight: 600; font-size: 27px; letter-spacing: .2px; margin-top: 14px; white-space: nowrap; }
  .card-front .brand { top: 112px; }
  .card-front .brand-mark { background: var(--lime); }
  .card-front .brand-name { color: var(--silver); }
  .card-back .brand { top: 185px; }
  .card-back .brand-mark { background: var(--white); }
  .card-back .brand-name { color: var(--white); font-size: 29px; }
  .person { position: absolute; top: 325px; left: 0; right: 0; }
  .person-name { color: var(--lime); font-weight: 700; font-size: 21px; letter-spacing: .4px; line-height: 26px; }
  .person-role { color: var(--ink); font-size: 15px; line-height: 20px; }
  .contacts { position: absolute; top: 385px; left: 0; right: 0; list-style: none; color: var(--ink); font-size: 15px; line-height: 20px; }
  .contacts .label { color: var(--lime); font-weight: 700; font-size: 16px; margin-right: 4px; }
  .address { position: absolute; top: 481px; left: 0; right: 0; color: var(--ink); font-size: 15px; line-height: 20px; font-style: normal; }
  .slogan { position: absolute; top: 346px; left: 0; right: 0; color: var(--white); font-size: 16px; letter-spacing: 3.4px; line-height: 20px; }
  .website { position: absolute; top: 469px; left: 0; right: 0; color: var(--white); font-weight: 700; font-size: 17px; letter-spacing: .5px; }
</style>
</head>
<body>
<main class="stage">
  <article class="card card-front">
    <div class="texture" role="img" aria-label="Faint white geometric prism panel pattern"></div>
    <div class="content">
      <div class="brand">
        <span class="brand-mark"></span>
        <span class="brand-name">Ripplecraft Facades</span>
      </div>
      <div class="person">
        <p class="person-name">MARCUS HALE</p>
        <p class="person-role">Managing Director</p>
      </div>
      <ul class="contacts">
        <li><span class="label">P:</span>044-987 654 321</li>
        <li><span class="label">M:</span>044-987 654 321</li>
        <li><span class="label">F:</span>044-987 654 321</li>
        <li><span class="label">E:</span>info@ripplecraftpanels.com</li>
      </ul>
      <address class="address">48 Kiln Street, Geelong<br>Australia, 3220.</address>
    </div>
  </article>

  <article class="card card-back">
    <div class="texture" role="img" aria-label="Faint green geometric prism panel pattern"></div>
    <div class="content">
      <div class="brand">
        <span class="brand-mark"></span>
        <span class="brand-name">Ripplecraft Facades</span>
      </div>
      <p class="slogan">decorative panels for<br>interiors &amp; landscapes</p>
      <p class="website">WWW.RIPPLECRAFTPANELS.COM</p>
    </div>
  </article>
</main>
</body>
</html>
```